Wed site for biomedical device startup

We need a generic website for a medical device startup. I will provide examples below of websites from other companies that can serve as models for what we are looking for. The startup is for a device that can non invasively measure blood flow in the brain using light. The application is to detect the type of stroke someone is having before they get to the hospital so treatment can be started right away. This saves patients upto hours of delayed treatment. Patients will be able to recover from stroke much better and faster as a result. I have attached an AI generated illustration of what the device will ultimately look like for reference.

https://www.372clinicaltech.com
https://vextalune.com

Target Market(s)

Biomedical, medical device, investors of biomedical device startups

Industry/Entity Type

Biomedical

Coding

Coded - Design and coding required

Number of Pages Required

4 page

Requirements
Must have
• same section and section headings as example websites listed above
Nice to have
• similar to example websites listed above. Prefer a darker website over a lighter one. Perhaps dark blues to go with logo colors. A moving background image element at top of landing page could be cool. Something indicative of heartbeat, or neurons, or blood flow.

```html
<!DOCTYPE html>
<html lang="en">
<head>
<meta charset="utf-8">
<title>NVRA — Biomedical Innovation</title>
<link href="https://fonts.googleapis.com/css2?family=Saira:wght@400;500&family=Rubik:wght@400;500&display=swap" rel="stylesheet">
<style>
:root{
  --night:#07072b;
  --navy:#0f0d48;
  --indigo:#1c1466;
  --purple:#8c1fc8;
  --violet:#a526dc;
  --cyan:#17d5e8;
  --sky:#3a8ff0;
  --white:#ffffff;
  --soft:rgba(255,255,255,.86);
  --line:rgba(23,213,232,.55);
}
*{margin:0;padding:0;box-sizing:border-box}
html,body{width:1200px;height:3297px;overflow:hidden}
body{
  position:relative;
  font-family:"Rubik",sans-serif;color:var(--white);
  background:
    radial-gradient(ellipse 700px 420px at 600px 250px,rgba(120,40,160,.45),transparent 70%),
    radial-gradient(ellipse 600px 400px at 1100px 1300px,rgba(150,40,200,.45),transparent 70%),
    radial-gradient(ellipse 600px 500px at 100px 2800px,rgba(60,30,140,.45),transparent 70%),
    linear-gradient(180deg,#1d1760 0%,var(--navy) 18%,var(--night) 32%,#14104f 45%,var(--night) 58%,#120f4c 80%,var(--night) 100%);
}
.abs{position:absolute}
.display{font-family:"Saira",sans-serif;font-weight:400;letter-spacing:.5px}

/* brand */
.brand{display:flex;align-items:center;gap:14px}
.brand-dot{width:74px;height:74px;border-radius:50%;background:var(--violet)}
.brand-name{font-family:"Saira",sans-serif;font-weight:400;font-size:62px;letter-spacing:4px;line-height:1;color:var(--white)}

/* nav */
.nav{left:461px;top:58px;width:627px;height:38px;border-bottom:1px solid rgba(255,255,255,.25)}
.nav a{position:absolute;top:0;font-size:16px;color:var(--white);text-decoration:none}
.nav a.active{color:var(--cyan);font-weight:500}

/* hero */
.hero-glow{left:0;top:0;width:1200px;height:560px;
  background:radial-gradient(ellipse 520px 300px at 520px 200px,rgba(170,60,140,.28),transparent 70%),
             radial-gradient(ellipse 400px 260px at 1050px 150px,rgba(90,60,190,.3),transparent 70%)}
.hero-kicker{top:203px;width:1200px;text-align:center;font-size:36px;line-height:44px}
.hero-title{top:252px;width:1200px;text-align:center;font-size:64px;line-height:72px;font-weight:500}
.hero-sub{top:328px;width:1200px;text-align:center;font-size:20px;font-weight:500}

.btn{display:flex;align-items:center;justify-content:center;gap:14px;height:43px;border-radius:22px;
  background:linear-gradient(90deg,#9b1fd4 0%,#7a3ae0 50%,var(--sky) 85%,var(--cyan) 100%);
  color:var(--white);font-size:16px;font-weight:500;text-decoration:none}
.btn.cyan{background:var(--cyan)}
.btn svg{width:15px;height:15px}

/* section headings */
.heading{font-size:40px;line-height:48px}
.rule{height:2px;background:var(--cyan);width:104px}
.copy{font-size:14.5px;line-height:28px;text-align:justify;color:var(--white)}
.copy p+p{margin-top:20px}

/* who we are */
.who-art{left:134px;top:607px;width:419px;height:419px;border-radius:50%;
  background:radial-gradient(circle at 70% 25%,#2fd2ea 0%,#5a8ae8 40%,#9c38d8 80%,#8a28c8 100%)}

/* services */
.card{width:230px;height:352px;top:1302px;border:1px solid var(--line);border-radius:115px;text-align:center}
.card.featured{background:linear-gradient(180deg,#8e24d2 0%,#5b7be8 55%,var(--cyan) 100%);border-color:transparent}
.card-photo{position:absolute;left:26px;top:20px;width:178px;height:178px;border-radius:50%}
.card h3{position:absolute;top:217px;left:0;width:100%;font-family:"Saira",sans-serif;font-weight:400;font-size:15px;text-transform:uppercase}
.card p{position:absolute;top:246px;left:16px;right:16px;font-size:12.5px;line-height:21px;color:var(--soft)}
.card.featured h3,.card.featured p{color:#e9fbff}
.card .go{position:absolute;top:318px;left:108px;width:14px;height:14px}

/* how we help */
.help-photo{left:649px;top:1911px;width:422px;height:422px;border-radius:50%;
  background:linear-gradient(135deg,#3a5ea8 0%,#8fb6d8 40%,#2a3f7a 75%,#1b2c5e 100%)}
.help-ring{left:632px;top:1894px;width:456px;height:456px;border-radius:50%;border:3px solid var(--cyan)}

/* form */
.field{border:1px solid var(--line);border-radius:22px;height:44px;width:302px;display:flex;align-items:center;justify-content:space-between;padding:0 28px;font-size:13px}
.field svg{width:13px;height:13px;fill:var(--white)}
.field.area{height:175px;align-items:flex-start;padding-top:14px;border-radius:22px}

/* footer */
.foot-rule{left:111px;top:3012px;width:977px;height:1px;background:rgba(255,255,255,.18)}
.foot-links{top:3162px;left:0;width:1200px;display:flex;justify-content:center;gap:30px;font-size:14.5px}
.foot-links span.sep{opacity:.9}
.social{top:3205px;left:0;width:1200px;display:flex;justify-content:center;gap:13px}
.social i{width:31px;height:31px;border-radius:50%;background:#5b22b0;display:block}
.legal{top:3257px;width:1200px;text-align:center;font-size:10px}
</style>
</head>
<body>

<div class="abs hero-glow" role="img" aria-label="Soft background of glowing neurons"></div>

<!-- header -->
<div class="abs brand" style="left:111px;top:42px">
  <span class="brand-dot"></span><span class="brand-name">NVRA</span>
</div>
<nav class="abs nav">
  <a class="active" style="left:55px">HOME</a>
  <a style="left:153px">About Us</a>
  <a style="left:271px">Technology</a>
  <a style="left:406px">Publications</a>
  <a style="left:548px">Contact Us</a>
</nav>

<!-- hero -->
<div class="abs display hero-kicker">SHAPING THE FUTURE OF</div>
<h1 class="abs display hero-title">BIOMEDICAL INNOVATION</h1>
<div class="abs hero-sub">Cutting-edge solutions in diagnostics, data, and discovery</div>
<a class="abs btn" style="left:366px;top:381px;width:248px">Explore Our Technology
  <svg viewBox="0 0 16 16"><circle cx="8" cy="8" r="8" fill="#fff"/><path d="M5 8h5M8 5l3 3-3 3" stroke="#7a3ae0" stroke-width="2" fill="none"/></svg></a>
<a class="abs btn" style="left:644px;top:381px;width:189px">Contact Us
  <svg viewBox="0 0 16 16"><circle cx="8" cy="8" r="8" fill="#fff"/><path d="M5 8h5M8 5l3 3-3 3" stroke="#7a3ae0" stroke-width="2" fill="none"/></svg></a>

<!-- who we are -->
<div class="abs who-art" role="img" aria-label="Illustration of a waveform over a medical scene"></div>
<h2 class="abs display heading" style="left:627px;top:627px">WHO WE ARE</h2>
<div class="abs rule" style="left:627px;top:688px"></div>
<div class="abs copy" style="left:627px;top:710px;width:438px">
  <p>We are a science-driven team committed to accelerating breakthroughs in biomedical research and healthcare through technology, data, and innovation.</p>
  <p>Sed ut perspiciatis unde omnis iste natus error sit voluptatem accusantium doloremque laudantium, totam rem aperiam, eaque ipsa quae ab illo inventore veritatis et quasi architecto beatae vitae dicta sunt explicabo.</p>
</div>
<a class="abs btn" style="left:627px;top:952px;width:190px">Explore More
  <svg viewBox="0 0 16 16"><circle cx="8" cy="8" r="8" fill="#fff"/><path d="M5 8h5M8 5l3 3-3 3" stroke="#7a3ae0" stroke-width="2" fill="none"/></svg></a>

<!-- services -->
<h2 class="abs display heading" style="left:0;top:1161px;width:1200px;text-align:center">SERVICES WE OFFER</h2>
<div class="abs rule" style="left:548px;top:1223px"></div>
<div class="abs" style="top:1244px;width:1200px;text-align:center;font-size:15px">Ut enim ad minima veniam, quis nostrum exercitationem ullam corporis suscipit laboriosam</div>

<div class="abs card" style="left:111px">
  <div class="card-photo" role="img" aria-label="Photo of a researcher at a microscope" style="background:linear-gradient(135deg,#bfe6f5,#3b8fd8 60%,#1d4a9a)"></div>
  <h3>Biomarker Discovery</h3>
  <p>Ut enim ad minima veniam, quis nostrum exercitationem ullam corporis suscipit</p>
  <svg class="go" viewBox="0 0 16 16"><circle cx="8" cy="8" r="8" fill="#17d5e8"/><path d="M5 8h5M8 5l3 3-3 3" stroke="#0f0d48" stroke-width="2" fill="none"/></svg>
</div>
<div class="abs card" style="left:362px">
  <div class="card-photo" role="img" aria-label="Photo of a laboratory with glassware" style="background:linear-gradient(135deg,#dfe7f0,#8aa5c4 50%,#3d5680)"></div>
  <h3>Assay Development</h3>
  <p>Ut enim ad minima veniam, quis nostrum exercitationem ullam corporis suscipit</p>
  <svg class="go" viewBox="0 0 16 16"><circle cx="8" cy="8" r="8" fill="#17d5e8"/><path d="M5 8h5M8 5l3 3-3 3" stroke="#0f0d48" stroke-width="2" fill="none"/></svg>
</div>
<div class="abs card featured" style="left:611px">
  <div class="card-photo" role="img" aria-label="Photo of a patient monitor display" style="background:linear-gradient(135deg,#1a2a5a,#2d6fb0 50%,#c04a6a)"></div>
  <h3>Clinical Trial Support</h3>
  <p>Ut enim ad minima veniam, quis nostrum exercitationem ullam corporis suscipit</p>
  <svg class="go" viewBox="0 0 16 16"><circle cx="8" cy="8" r="8" fill="#8c1fc8"/><path d="M5 8h5M8 5l3 3-3 3" stroke="#fff" stroke-width="2" fill="none"/></svg>
</div>
<div class="abs card" style="left:859px">
  <div class="card-photo" role="img" aria-label="Photo of a digital health data display" style="background:radial-gradient(circle,#3fb8f0,#0d3f8a 60%,#061a45)"></div>
  <h3>Data Analysis</h3>
  <p>Ut enim ad minima veniam, quis nostrum exercitationem ullam corporis suscipit</p>
  <svg class="go" viewBox="0 0 16 16"><circle cx="8" cy="8" r="8" fill="#17d5e8"/><path d="M5 8h5M8 5l3 3-3 3" stroke="#0f0d48" stroke-width="2" fill="none"/></svg>
</div>

<!-- how we help band -->
<svg class="abs" style="left:0;top:1770px" width="1200" height="700" viewBox="0 0 1200 700">
  <path d="M90 99 Q600 -65 1107 99 Q600 -19 90 99Z" fill="#17d5e8"/>
  <path d="M90 604 Q600 766 1107 604 Q600 720 90 604Z" fill="#17d5e8"/>
  <path d="M0 124 Q600 -28 1200 124 L1200 579 Q600 733 0 579Z" fill="#8c1fc8"/>
</svg>
<h2 class="abs display heading" style="left:110px;top:1934px">HOW WE HELP</h2>
<div class="abs rule" style="left:110px;top:1995px"></div>
<div class="abs copy" style="left:110px;top:2017px;width:438px">
  <p>We are a science-driven team committed to accelerating breakthroughs in biomedical research and healthcare through technology, data, and innovation.</p>
  <p>Sed ut perspiciatis unde omnis iste natus error sit voluptatem accusantium doloremque laudantium, totam rem aperiam, eaque ipsa quae ab illo inventore veritatis et quasi architecto beatae vitae dicta sunt explicabo.</p>
</div>
<a class="abs btn cyan" style="left:110px;top:2259px;width:190px">Explore More
  <svg viewBox="0 0 16 16"><circle cx="8" cy="8" r="8" fill="#fff"/><path d="M5 8h5M8 5l3 3-3 3" stroke="#17d5e8" stroke-width="2" fill="none"/></svg></a>
<div class="abs help-ring"></div>
<div class="abs help-photo" role="img" aria-label="Photo of scientists working with samples in a lab"></div>

<!-- stay connected -->
<h2 class="abs display heading" style="left:0;top:2532px;width:1200px;text-align:center">STAY CONNECTED</h2>
<div class="abs rule" style="left:548px;top:2594px"></div>
<div class="abs" style="left:250px;top:2612px;width:700px;text-align:center;font-size:15.5px;line-height:28px">Join our community to receive updates about our latest developments and research in blood loss monitoring technology.</div>

<div class="abs field" style="left:282px;top:2696px">First Name
  <svg viewBox="0 0 16 16"><circle cx="8" cy="4.5" r="3.5"/><path d="M1 16c0-4 3-7 7-7s7 3 7 7z"/></svg></div>
<div class="abs field" style="left:282px;top:2762px">Email Address
  <svg viewBox="0 0 16 16"><rect x="0" y="3" width="16" height="11" rx="1"/><path d="M0 4l8 5 8-5" stroke="#0f0d48" stroke-width="1.5" fill="none"/></svg></div>
<div class="abs field" style="left:282px;top:2826px">Contact Number
  <svg viewBox="0 0 16 16"><path d="M3 1l3 3-2 2c1 2 3 4 5 5l2-2 3 3-2 3C6 15 1 10 1 3z"/></svg></div>
<div class="abs field area" style="left:616px;top:2696px">Comments
  <svg viewBox="0 0 16 16"><ellipse cx="8" cy="7" rx="7.5" ry="5.5"/><path d="M3 11l-1 4 4-2z"/></svg></div>
<a class="abs btn" style="left:506px;top:2900px;width:189px">Submit Here
  <svg viewBox="0 0 16 16"><circle cx="8" cy="8" r="8" fill="#fff"/><path d="M5 8h5M8 5l3 3-3 3" stroke="#7a3ae0" stroke-width="2" fill="none"/></svg></a>

<!-- footer -->
<div class="abs foot-rule"></div>
<div class="abs brand" style="left:460px;top:3058px">
  <span class="brand-dot" style="width:76px;height:76px"></span><span class="brand-name">NVRA</span>
</div>
<div class="abs foot-links">
  <span>Home</span><span class="sep">/</span><span>About Us</span><span class="sep">/</span><span>Technology</span><span class="sep">/</span><span>How We Help</span><span class="sep">/</span><span>Contact Us</span>
</div>
<div class="abs social"><i></i><i></i><i></i><i></i><i></i></div>
<div class="abs legal">(C) Copyright | All Rights Reserved</div>

</body>
</html>
```